Web Design For Staffing Company

We need a homepage web design for a technical staffing company.

Please see attached brief for project details.

please make the site modern with bold colors while matching the logo

Be sure to read the attached breif in full beforehand.

Target Market(s)

technical companies looking to hire talent

Industry/Entity Type

Staffing

Number of Pages Required

1 page

Font styles to use
Sans Serif

```html
<!DOCTYPE html>
<html lang="en">
<head>
<meta charset="utf-8">
<title>Veltrix Staffing</title>
<link href="https://fonts.googleapis.com/css2?family=Poppins:wght@400;500;600&family=Lato:wght@400&display=swap" rel="stylesheet">
<style>
:root{
  --blue:#3a87d6;
  --blue-mid:#3a8ddb;
  --blue-deep:#2e73bd;
  --navy:#1f3f73;
  --ink:#222;
  --text:#333;
  --grey-bg:#e9e9e9;
  --light-bg:#f3f3f3;
  --footer:#1b1b1b;
  --white:#fff;
}
*{margin:0;padding:0;box-sizing:border-box}
html,body{width:1200px;height:3322px;overflow:hidden}
body{font-family:"Poppins",sans-serif;color:var(--text);background:var(--white);position:relative}
.abs{position:absolute}
.btn{position:absolute;display:flex;align-items:center;justify-content:center;background:var(--blue);color:var(--white);font-family:"Poppins",sans-serif;font-weight:500;font-size:18px;height:48px}
/* header */
.header{position:absolute;top:0;left:0;width:1200px;height:92px;background:var(--white)}
.logo{position:absolute;left:143px;top:22px;display:flex;align-items:center;gap:10px}
.logo-mark{width:36px;height:36px;border-radius:50%;background:var(--blue)}
.logo-name{font-weight:600;font-size:30px;color:var(--navy);line-height:1}
.nav{position:absolute;top:37px;left:570px;display:flex;gap:39px;font-size:15px;color:#333}
.nav .active{color:var(--blue)}
.search-bar{position:absolute;top:92px;left:0;width:1200px;height:48px;background:var(--blue);color:var(--white);font-size:16px}
.search-bar .right{position:absolute;left:600px;top:0;width:600px;height:48px;background:#2f7bc9}
/* hero */
.hero{position:absolute;top:140px;left:0;width:1200px;height:474px;background:linear-gradient(135deg,#7d8591,#4a5260 55%,#8a8f95)}
.hero h1{position:absolute;top:148px;width:100%;text-align:center;color:var(--white);font-weight:600;font-size:34px;line-height:53px}
.arrow-circle{position:absolute;top:217px;width:40px;height:40px;border-radius:50%;background:var(--white)}
.intro{position:absolute;top:682px;left:130px;width:940px;text-align:center;font-size:20.5px;line-height:40px;color:var(--ink)}
/* split panels */
.split{position:absolute;left:0;width:1200px;height:440px}
.split .pane-text{position:absolute;top:0;width:600px;height:440px;background:var(--grey-bg)}
.split .pane-photo{position:absolute;top:0;width:600px;height:440px}
.pane-copy{position:absolute;width:430px}
.pane-copy p{font-family:"Lato",sans-serif;font-size:16px;line-height:32px;color:var(--ink)}
.pane-actions{display:flex;gap:8px;margin-top:24px}
.pane-actions .btn{position:static;width:152px}
.section-title{position:absolute;width:100%;text-align:center;color:var(--blue);font-weight:600;font-size:42px}
.testimonial-name{position:absolute;top:1902px;width:100%;text-align:center;font-size:23px;color:#111}
.testimonial-role{position:absolute;top:1938px;width:100%;text-align:center;font-size:12px;color:#222}
.testimonial-quote{position:absolute;top:1966px;left:130px;width:940px;text-align:center;font-size:16.5px;line-height:32px;color:var(--blue)}
.dots{position:absolute;top:2076px;left:546px;display:flex;gap:20px}
.dots span{width:12px;height:12px;border-radius:50%;background:#aaa}
.dots span:first-child{background:var(--blue)}
.blog{position:absolute;top:2168px;left:0;width:1200px;height:570px;background:var(--light-bg)}
.card{position:absolute;top:149px;width:296px;height:328px;background:var(--white)}
.card .photo{width:296px;height:200px}
.card .date{position:absolute;top:218px;left:16px;font-size:12px;color:#333}
.card .title{position:absolute;top:242px;left:16px;width:270px;font-size:16.5px;line-height:24px;color:var(--blue)}
.card.raised{box-shadow:0 2px 8px rgba(0,0,0,.25)}
.cta{position:absolute;top:2738px;width:600px;height:279px;text-align:center;color:var(--white)}
.cta h2{margin-top:66px;font-weight:500;font-size:29px;line-height:42px}
.cta .dark-btn{display:inline-block;margin-top:18px;background:#1c1c1c;color:var(--white);font-weight:500;font-size:19px;padding:10px 32px}
.footer{position:absolute;top:3017px;left:0;width:1200px;height:305px;background:var(--footer);color:var(--white)}
.fcol{position:absolute;top:52px;width:240px}
.fcol h3{font-weight:500;font-size:18px}
.fcol p{margin-top:6px;font-size:10.5px;line-height:17px;color:#bbb}
.fcol .outline{display:inline-block;margin-top:20px;border:1px solid #888;font-size:12px;padding:12px 17px;color:#ddd}
.rule{position:absolute;top:213px;left:143px;width:913px;height:1px;background:#444}
.copy{position:absolute;top:254px;left:144px;font-size:11px;color:#aaa}
.social{position:absolute;top:250px;left:944px;display:flex;gap:26px}
.social span{width:20px;height:20px;border-radius:50%;background:#888}
</style>
</head>
<body>
<header class="header">
  <div class="logo"><span class="logo-mark"></span><span class="logo-name">Veltrix</span></div>
  <nav class="nav"><span class="active">HOME</span><span>ABOUT</span><span>JOB SEEKERS</span><span>CLIENTS</span><span>CONTACT</span></nav>
</header>
<div class="search-bar">
  <span class="abs" style="left:143px;top:14px">Keyword</span>
  <div class="right">
    <svg class="abs" style="left:24px;top:15px" width="12" height="17" viewBox="0 0 12 17"><path d="M6 0a6 6 0 0 0-6 6c0 4.5 6 11 6 11s6-6.5 6-11a6 6 0 0 0-6-6zm0 8.5A2.5 2.5 0 1 1 6 3.5a2.5 2.5 0 0 1 0 5z" fill="#fff"/></svg>
    <span class="abs" style="left:40px;top:14px">Location</span>
    <svg class="abs" style="left:436px;top:13px" width="20" height="20" viewBox="0 0 20 20"><circle cx="8" cy="8" r="6" fill="none" stroke="#fff" stroke-width="2.6"/><path d="M12.5 12.5 18 18" stroke="#fff" stroke-width="3" stroke-linecap="round"/></svg>
  </div>
</div>
<section class="hero" role="img" aria-label="Office desk with two people handing over a document beside a keyboard and monitor">
  <h1>The Right People For The Right Jobs!<br>Bridging the talent gap in Technical Staffing</h1>
  <span class="btn" style="left:444px;top:269px;width:152px">HIRE TALENT</span>
  <span class="btn" style="left:605px;top:269px;width:150px">GET HIRED</span>
  <span class="arrow-circle" style="left:47px"><svg width="40" height="40"><path d="M23 12 15 20l8 8" fill="none" stroke="#111" stroke-width="3.5"/></svg></span>
  <span class="arrow-circle" style="left:1111px"><svg width="40" height="40"><path d="M17 12l8 8-8 8" fill="none" stroke="#111" stroke-width="3.5"/></svg></span>
</section>
<p class="intro">Veltrix Staffing is a National Technical Staffing and Recruiting Solutions Provider founded in2013 focused on matching contract and full time Engineering and IT professionals with new andexciting employment opportunities!</p>

<section class="split" style="top:878px">
  <div class="pane-text" style="left:0">
    <div class="pane-copy" style="left:143px;top:72px">
      <p>Simply said... WE LOVE TO RECRUIT! It's our passion and we take it very seriously! It is noteasy for JOB SEEK-ERS to put their job search efforts and trust in the hands of someone else,especially when there are so many Staffing Firms to choose from. So how do you know you arechoosing the best Staffing Representation possible?</p>
      <div class="pane-actions"><span class="btn">LEARN MORE</span><span class="btn">VIEW JOBS</span></div>
    </div>
  </div>
  <div class="pane-photo" style="left:600px;background:linear-gradient(135deg,#6b5446,#8d7a6c 45%,#3f5a86)" role="img" aria-label="Smiling professional in glasses shaking hands in an office"></div>
</section>
<section class="split" style="top:1318px">
  <div class="pane-photo" style="left:0;background:linear-gradient(135deg,#d8d8d6,#c2b39e 50%,#e6e6e4)" role="img" aria-label="Woman in glasses working on a laptop at a white desk with a plant"></div>
  <div class="pane-text" style="left:600px">
    <div class="pane-copy" style="left:44px;top:88px;width:425px">
      <p>Are you responsible for Technical Staffing within your organization?&nbsp; Are you satisfied with yourcurrent Sup-plier(s)' overall performance?&nbsp; Does it appear they iden-tify potential Candidate(s)based purely on "buzz-word" searches?&nbsp; Is it evident they just do not grasp the scope andresponsibilities of your technical staffing need(s)?</p>
      <div class="pane-actions"><span class="btn">LEARN MORE</span><span class="btn">HIRE TALENT</span></div>
    </div>
  </div>
</section>

<h2 class="section-title" style="top:1826px">Testimonials</h2>
<div class="testimonial-name">Sam R.</div>
<div class="testimonial-role">Electrical Test Engineer in the Automotive Sector:</div>
<p class="testimonial-quote">"Mark Dalen is an excellent recruiter. He is articulate, honest, has a good nature and is aneffective information conduit between his clients and candidates. He gave me the feeling he is there for the big picture desiring to forge a future relationship that will be mutually beneficial toboth of us. "</p>
<div class="dots"><span></span><span></span><span></span><span></span></div>

<section class="blog">
  <h2 class="section-title" style="top:70px">Veltrix Blog</h2>
  <svg class="abs" style="left:54px;top:300px" width="24" height="40"><path d="M20 4 6 20l14 16" fill="none" stroke="#555" stroke-width="4"/></svg>
  <svg class="abs" style="left:1122px;top:300px" width="24" height="40"><path d="M4 4l14 16L4 36" fill="none" stroke="#555" stroke-width="4"/></svg>
  <article class="card raised" style="left:143px">
    <div class="photo" style="background:linear-gradient(90deg,#777,#222)" role="img" aria-label="Black and white portrait with a quotation about technology"></div>
    <span class="date">27 June, 2020</span>
    <span class="title">Tips for Spotting a U.S. Recession Before It Becomes Official</span>
  </article>
  <article class="card" style="left:452px">
    <div class="photo" style="background:linear-gradient(135deg,#b9a89a,#5a4a44 55%,#8b7566)" role="img" aria-label="Woman typing on a laptop in a café"></div>
    <span class="date">27 June, 2020</span>
    <span class="title">Ways To Make The Most Of The Hot Job Market</span>
  </article>
  <article class="card" style="left:760px">
    <div class="photo" style="background:linear-gradient(135deg,#8fb0cf,#d9c3b1 50%,#2f4a72)" role="img" aria-label="Business handshake over a desk with a tablet"></div>
    <span class="date">27 June, 2020</span>
    <span class="title">Back To Basics: Meeting Employ-ees' Needs To Improve Organiza-tional Performance</span>
  </article>
</section>

<section class="cta" style="left:0;background:var(--blue-mid)">
  <h2>Looking for career-minded<br>candidates?</h2>
  <span class="dark-btn">Request Talent</span>
</section>
<section class="cta" style="left:600px;background:var(--blue-deep)">
  <h2>Looking for career<br>opportunities?</h2>
  <span class="dark-btn">Search Jobs</span>
</section>

<footer class="footer">
  <div class="fcol" style="left:147px"><h3>GET HIRED</h3><p>Curabitur eu erat dignissim, varius<br>ipsum non, dictum turpis.</p><span class="outline">SEARCH NOW</span></div>
  <div class="fcol" style="left:500px"><h3>HIRE TALENT</h3><p>Curabitur eu erat dignissim, varius<br>ipsum non, dictum turpis.</p><span class="outline">START TODAY</span></div>
  <div class="fcol" style="left:854px"><h3>ADDRESS</h3><p>Veltrix Staffing, Inc.120 Harbor Street,<br>Suite 4, Lakeview, MA 01999</p><span class="outline">CONTACT US</span></div>
  <div class="rule"></div>
  <div class="copy">Copyright &copy; 2020 &nbsp;Veltrix Staffing. &nbsp;&nbsp;All rights reserved.</div>
  <div class="social" aria-label="Social links"><span></span><span></span><span></span></div>
</footer>
</body>
</html>
```